We need a logo for our business which is a dental clinic (i.e. dentistry).
We would lilke designs using the colour blue, green and black incorporating the words Corvath Dental, possibly a smile or a tooth image can be considered for incorporation in the logo.

Industry/Entity Type

Dental

```html
<!DOCTYPE html>
<html lang="en">
<head>
<meta charset="utf-8">
<title>Corvath Dental – Business Cards</title>
<link href="https://fonts.googleapis.com/css2?family=Michroma&display=swap" rel="stylesheet">
<style>
  :root {
    --bg: #cfcfcf;
    --green: #2d8a2f;
    --green-dark: #1f6e22;
    --white: #ffffff;
    --light-grey: #ececec;
    --mid-grey: #8a8a8a;
    --dark-grey: #4a4a4a;
    --text-dark: #2b2b2b;
  }
  html, body {
    margin: 0;
    padding: 0;
    width: 1200px;
    height: 907px;
    overflow: hidden;
    background: var(--bg);
    font-family: "Michroma", sans-serif;
  }
  .stage {
    position: relative;
    width: 1200px;
    height: 907px;
  }
  .card {
    position: absolute;
    top: 150px;
    width: 350px;
    height: 600px;
    display: flex;
    flex-direction: column;
    box-shadow: 0 12px 30px rgba(0,0,0,0.25);
    overflow: hidden;
  }
  .card--back { left: 205px; }
  .card--front { left: 645px; }
  .band {
    display: flex;
    align-items: center;
    justify-content: center;
    box-sizing: border-box;
  }
  .band--green {
    background: linear-gradient(180deg, var(--green) 0%, var(--green-dark) 100%);
    color: var(--white);
  }
  .band--grey { background: linear-gradient(180deg, #6e6e6e, var(--dark-grey)); }
  .band--white { background: var(--white); }
  .band--light { background: var(--light-grey); color: var(--text-dark); }

  .brand {
    display: flex;
    align-items: center;
    gap: 12px;
  }
  .brand__dot {
    width: 16px;
    height: 16px;
    border-radius: 50%;
    background: var(--green);
  }
  .brand__name {
    color: var(--green);
    font-size: 22px;
    line-height: 1.25;
    letter-spacing: 1px;
    text-transform: uppercase;
  }
  .website {
    font-size: 13px;
    letter-spacing: 0.5px;
  }

  /* back */
  .card--back .band--grey { height: 110px; }
  .card--back .band--white { flex: 1; }
  .card--back .band--green { height: 110px; }

  /* front */
  .name-band { height: 90px; flex-direction: column; }
  .person__name { font-size: 20px; letter-spacing: 1px; }
  .person__role { font-size: 8px; letter-spacing: 1px; margin-top: 6px; }
  .logo-band { height: 150px; }
  .phone-band { height: 110px; gap: 16px; }
  .phone-band .lines { font-size: 14px; line-height: 1.6; }
  .email-band { height: 100px; flex-direction: column; gap: 10px; font-size: 14px; }
  .address-band { flex: 1; flex-direction: column; justify-content: space-between; padding: 22px 0 16px; }
  .address { display: flex; align-items: center; gap: 12px; font-size: 12px; line-height: 1.7; }
  .web-strip {
    width: 300px;
    height: 36px;
    background: var(--dark-grey);
    color: var(--white);
    display: flex;
    align-items: center;
    justify-content: center;
  }
  .icon { flex: none; }
</style>
</head>
<body>
<main class="stage">
  <section class="card card--back" aria-label="Card back">
    <div class="band band--grey"></div>
    <div class="band band--white">
      <div class="brand">
        <span class="brand__dot"></span>
        <span class="brand__name">Corvath<br>Dental</span>
      </div>
    </div>
    <div class="band band--green">
      <span class="website">www.corvathdental.com</span>
    </div>
  </section>

  <section class="card card--front" aria-label="Card front">
    <div class="band band--green name-band">
      <span class="person__name">DANIEL HARTLEY</span>
      <span class="person__role">GENERAL MANAGER</span>
    </div>
    <div class="band band--white logo-band">
      <div class="brand">
        <span class="brand__dot"></span>
        <span class="brand__name">Corvath<br>Dental</span>
      </div>
    </div>
    <div class="band band--green phone-band">
      <svg class="icon" width="18" height="18" viewBox="0 0 24 24" aria-hidden="true">
        <path fill="#fff" d="M6.6 10.8a15.1 15.1 0 0 0 6.6 6.6l2.2-2.2c.3-.3.7-.4 1-.2 1.1.4 2.3.6 3.6.6.6 0 1 .4 1 1V20c0 .6-.4 1-1 1A17 17 0 0 1 3 4c0-.6.4-1 1-1h3.5c.6 0 1 .4 1 1 0 1.3.2 2.5.6 3.6.1.3 0 .7-.2 1z"/>
      </svg>
      <div class="lines">012 555 0147<br>012 555 0147</div>
    </div>
    <div class="band band--light email-band">
      <svg class="icon" width="22" height="16" viewBox="0 0 22 16" aria-hidden="true">
        <rect x="0.5" y="0.5" width="21" height="15" fill="#3a3a3a"/>
        <path d="M1 1l10 8 10-8" fill="none" stroke="#ececec" stroke-width="1.4"/>
      </svg>
      <span>hello@corvathdental.com</span>
    </div>
    <div class="band band--green address-band">
      <div class="address">
        <svg class="icon" width="14" height="20" viewBox="0 0 14 20" aria-hidden="true">
          <path fill="#fff" d="M7 0a7 7 0 0 0-7 7c0 5 7 13 7 13s7-8 7-13a7 7 0 0 0-7-7zm0 9.5A2.5 2.5 0 1 1 7 4.5a2.5 2.5 0 0 1 0 5z"/>
        </svg>
        <span>42 Marlow Road,<br>2nd Floor Suite B</span>
      </div>
      <div class="web-strip"><span class="website">www.corvathdental.com</span></div>
    </div>
  </section>
</main>
</body>
</html>
```